Kelp Row Arc need a business card designed

Descriptions:

Kelp Row Arc is a recruiting firm that only recruits sales people. Our advantage In the market is that we use A.I. software to recruit and pre assess candidates to find the top 20% of talent.

Here is the copy needed on each side of the card

Side #1.

Photo/Headshot
THOMAS MERROW
CEO
555-318-4427
www.KelpRowArc.example
tmerrow@KelpRowArc.example
Quillmere, WA

"Finding & Hiring Sales People Sucks!"
"Using the power of A.I. assessment tools to find you the top 20% of sales talent guaranteed!"

Side 2.

"The True cost of a bad hire can be as high as 10 X the first year salary"

"With KELP ROW ARC:
50% Faster time to hire
83% New Hire retention
96% Of wrong hires eliminated
50% Lower sales turnover

Link to ZIP guidelines / Templates for PhotoShop, InDesgin & Illustrator:
https://www.filevaultly.example/scl/fo/qpzt7yrnwke2lsa4cdjbv/h?rlkey=tnw83kfpqzr1c5vyxlbe2ad9&dl=0

```html
<!DOCTYPE html>
<html lang="en">
<head>
<meta charset="utf-8">
<title>Kelp Row Arc – Business Card</title>
<link rel="stylesheet" href="https://fonts.googleapis.com/css2?family=Open+Sans:wght@300;400;600;700;800&display=swap">
<style>
  :root {
    --stage: #e9e6e1;
    --navy: #063478;
    --sky: #0d96dc;
    --sky-text: #2c9de3;
    --royal: #1a4fa6;
    --charcoal: #242529;
    --charcoal-deep: #1b1c1f;
    --charcoal-mid: #202124;
    --photo-light: #e6e6e6;
    --photo-dark: #cfd2d6;
    --white: #ffffff;
  }
  * { box-sizing: border-box; margin: 0; padding: 0; }
  html, body { width: 1200px; height: 780px; overflow: hidden; }
  body {
    background: var(--stage);
    font-family: "Open Sans", Arial, sans-serif;
    position: relative;
  }
  .card {
    position: absolute;
    top: 70px;
    width: 366px;
    height: 640px;
    border-radius: 26px;
    overflow: hidden;
    box-shadow: 0 10px 28px rgba(0,0,0,.25);
  }

  /* ---------- Back side ---------- */
  .card-back { left: 194px; background: var(--navy); }
  .back-content {
    position: absolute;
    left: -137px; top: 137px;
    width: 640px; height: 366px;
    transform: rotate(-90deg);
    transform-origin: center;
  }
  .back-brand {
    position: absolute; left: 46px; top: 40px;
    display: flex; align-items: center; gap: 14px;
    font-size: 62px; font-weight: 300; letter-spacing: 2px;
    color: var(--sky-text); line-height: 1;
  }
  .back-brand .brand-mark { width: 26px; height: 26px; background: var(--sky-text); }
  .back-tagline {
    position: absolute; right: 40px; top: 112px;
    font-size: 13px; font-weight: 700; letter-spacing: 1.5px;
    color: var(--sky-text);
  }
  .back-lead {
    position: absolute; left: 0; right: 0; top: 158px;
    text-align: center; font-size: 19px; font-weight: 700;
    color: var(--sky-text); letter-spacing: .5px;
  }
  .back-stats {
    position: absolute; left: 0; right: 0; top: 194px;
    list-style: none; text-align: center;
    color: var(--white); font-size: 15.5px; line-height: 30px;
  }
  .back-stats .dot { color: var(--sky-text); margin: 0 6px; }
  .back-stripe {
    position: absolute; left: 0; right: 0; bottom: 0; height: 62px;
    background: var(--sky);
    display: flex; align-items: center; justify-content: center;
    color: var(--white); font-size: 16px; letter-spacing: .3px;
  }

  /* ---------- Front side ---------- */
  .card-front { left: 640px; background: var(--charcoal); color: var(--white); }
  .front-curves { position: absolute; inset: 0; }
  .front-brand {
    position: absolute; left: 34px; top: 46px;
    font-size: 30px; font-weight: 300; letter-spacing: 1px;
    color: var(--royal); line-height: 1;
  }
  .front-tagline {
    position: absolute; left: 150px; top: 82px;
    font-size: 8px; font-weight: 700; letter-spacing: 1px; color: var(--sky);
  }
  .headshot {
    position: absolute; left: 113px; top: 118px;
    width: 140px; height: 140px; border-radius: 50%;
    border: 3px solid var(--sky);
    background: linear-gradient(180deg, var(--photo-light) 0%, var(--photo-dark) 100%);
  }
  .person-name {
    position: absolute; left: 0; right: 0; top: 272px;
    text-align: center; font-size: 28px; font-weight: 800; letter-spacing: .5px;
  }
  .person-name .first { color: var(--royal); }
  .person-name .last { color: var(--sky); }
  .person-role {
    position: absolute; left: 0; right: 0; top: 312px;
    text-align: center; font-size: 15px; font-weight: 600;
  }
  .contact-icons {
    position: absolute; left: 0; right: 0; top: 340px;
    display: flex; justify-content: center; gap: 8px;
  }
  .contact-icons svg, .pin-icon { width: 24px; height: 24px; }
  .contact-list {
    position: absolute; left: 0; right: 0; top: 374px;
    list-style: none; text-align: center;
    font-size: 14px; line-height: 23px;
  }
  .pin-icon { position: absolute; left: 171px; top: 458px; }
  .location {
    position: absolute; left: 0; right: 0; top: 488px;
    text-align: center; font-size: 14px;
  }
  .front-quote {
    position: absolute; left: 26px; right: 26px; top: 560px;
    text-align: center; font-size: 13px; line-height: 19px;
  }
  .front-quote .headline { color: var(--sky-text); }
</style>
</head>
<body>

<section class="card card-back" aria-label="Card back">
  <div class="back-content">
    <div class="back-brand"><span class="brand-mark"></span>KELP ROW ARC</div>
    <div class="back-tagline">YOUR A.I. SALES RECRUITER</div>
    <p class="back-lead">With KELP ROW ARC</p>
    <ul class="back-stats">
      <li><span class="dot">●</span>50% Faster time to hire <span class="dot">●</span>83% New Hire retention</li>
      <li><span class="dot">●</span>96% Of wrong hires eliminated <span class="dot">●</span>50% Lower sales turnover</li>
    </ul>
    <p class="back-stripe">"The True cost of a bad hire can be as high as 10 X the first year salary"</p>
  </div>
</section>

<section class="card card-front" aria-label="Card front">
  <svg class="front-curves" viewBox="0 0 366 640" preserveAspectRatio="none" aria-hidden="true">
    <path d="M0 560 C90 610 260 600 366 520 L366 640 L0 640 Z" fill="var(--charcoal-mid)"/>
    <path d="M0 420 C40 500 120 540 200 545 C280 548 340 520 366 470 L366 640 L0 640 Z" fill="var(--charcoal-deep)" opacity=".75"/>
    <path d="M30 300 C40 450 140 525 250 525 C310 525 350 500 366 470 L366 640 L0 640 L0 300 Z" fill="var(--charcoal-mid)" opacity=".6"/>
  </svg>

  <div class="front-brand">KELP ROW ARC</div>
  <div class="front-tagline">YOUR A.I. SALES RECRUITER</div>

  <div class="headshot" role="img" aria-label="Headshot photo of Thomas Merrow"></div>

  <h1 class="person-name"><span class="first">THOMAS</span> <span class="last">MERROW</span></h1>
  <p class="person-role">CEO</p>

  <div class="contact-icons">
    <svg viewBox="0 0 24 24" aria-label="Phone"><circle cx="12" cy="12" r="12" fill="var(--sky)"/><path d="M8 6.5l2 0 1 3-1.4 1a7 7 0 0 0 3.9 3.9l1-1.4 3 1v2a1.5 1.5 0 0 1-1.6 1.5A10 10 0 0 1 6.5 8.1 1.5 1.5 0 0 1 8 6.5z" fill="#fff"/></svg>
    <svg viewBox="0 0 24 24" aria-label="Email"><circle cx="12" cy="12" r="12" fill="var(--sky)"/><rect x="6" y="8" width="12" height="9" rx="1" fill="#fff"/><path d="M6.5 8.5 12 13l5.5-4.5" fill="none" stroke="var(--sky)" stroke-width="1.3"/></svg>
    <svg viewBox="0 0 24 24" aria-label="Website"><circle cx="12" cy="12" r="12" fill="var(--sky)"/><circle cx="12" cy="12" r="6" fill="none" stroke="#fff" stroke-width="1.4"/><ellipse cx="12" cy="12" rx="2.6" ry="6" fill="none" stroke="#fff" stroke-width="1.2"/><path d="M6 12h12" stroke="#fff" stroke-width="1.2"/></svg>
  </div>

  <ul class="contact-list">
    <li>555-318-4427</li>
    <li>www.KelpRowArc.example</li>
    <li>tmerrow@KelpRowArc.example</li>
  </ul>

  <svg class="pin-icon" viewBox="0 0 24 24" aria-label="Location"><circle cx="12" cy="12" r="12" fill="var(--sky)"/><path d="M12 5a4.5 4.5 0 0 0-4.5 4.5C7.5 13 12 18 12 18s4.5-5 4.5-8.5A4.5 4.5 0 0 0 12 5z" fill="#fff"/><circle cx="12" cy="9.5" r="1.6" fill="var(--sky)"/></svg>
  <p class="location">Quillmere, WA</p>

  <p class="front-quote">
    <span class="headline">"Finding &amp; Hiring Sales People Sucks!"</span><br>
    "Using the power of A.I. assessment tools to find you the top 20% of sales talent guaranteed!"
  </p>
</section>

</body>
</html>
```